American cannabis tech company business card design

Pavrel.com is seeking a modern, professional, and brand-aligned business card that represents our company and its core values: Mission, Story, Values, and Impact. As an innovative cannabis company, we want a business card that is not only visually appealing but also serves as a representation of who we are and what we stand for.

Project Scope: Design a double-sided business card that integrates our brand identity and core values. Incorporate our key brand elements, ensuring a sleek and contemporary aesthetic. Visually reflect our core values (Mission, Story, Values, Impact) in a way that is engaging yet professional.

Target Market(s)

Vendors, third parties,

Contact Information for Business Card

Contact details (name, title, email, phone, website, etc.)

Font styles to use
Other font styles liked:
• Caslon, Centra

Colors

Designer to choose colors to be used in the design.

Requirements
Must have
• Pavrel.com logo and branding A creative yet clean way to integrate our core values (Mission, Story, Values, Impact) Modern typography and a well-structured layout
Nice to have
• forest green, grey, white, black
Should not have
• references to marijuana, leafs, plants, or related product

```html
<!DOCTYPE html>
<html lang="en">
<head>
<meta charset="utf-8">
<title>Pavrel.com Business Card</title>
<link rel="stylesheet" href="https://fonts.googleapis.com/css2?family=Poppins:wght@400;600;800&display=swap">
<style>
  :root {
    --forest: #1f4d2b;
    --forest-deep: #163a20;
    --paper: #f4f4f2;
    --paper-shade: #e3e3e0;
    --ink-light: #ffffff;
    --shadow: #0c1a10;
    --stage: #d9d9d6;
  }
  * { box-sizing: border-box; margin: 0; padding: 0; }
  html, body { width: 1200px; height: 780px; overflow: hidden; }
  body {
    background: var(--stage);
    font-family: "Poppins", Arial, sans-serif;
    display: flex;
    align-items: center;
    justify-content: center;
    gap: 60px;
  }
  .card {
    position: relative;
    width: 520px;
    height: 300px;
    border-radius: 16px;
    overflow: hidden;
    box-shadow: 0 10px 28px rgba(0,0,0,.22);
  }
  /* Front */
  .card-front {
    background: linear-gradient(135deg, #ffffff, var(--paper) 60%, var(--paper-shade));
    display: flex;
    align-items: center;
    justify-content: center;
  }
  .wordmark {
    font-weight: 800;
    font-size: 78px;
    letter-spacing: 2px;
    color: var(--forest);
  }
  /* Back */
  .card-back { background: var(--forest); color: var(--ink-light); }
  .back-curve { position: absolute; inset: 0; }
  .back-wordmark {
    position: absolute;
    right: 34px;
    top: 50%;
    transform: translateY(-50%);
    font-weight: 800;
    font-size: 34px;
    letter-spacing: 1px;
    color: var(--forest);
  }
  .edge-dot {
    position: absolute;
    left: -22px;
    top: 36px;
    width: 44px;
    height: 44px;
    border-radius: 50%;
    background: var(--paper);
  }
  .contact {
    position: absolute;
    left: 44px;
    top: 34px;
    width: 270px;
  }
  .person-name {
    font-weight: 600;
    font-size: 19px;
    text-transform: uppercase;
    letter-spacing: .5px;
  }
  .person-title { font-size: 13px; margin-bottom: 26px; }
  .address { font-size: 12.5px; line-height: 1.45; margin-bottom: 16px; }
  .contact-list { list-style: none; font-size: 12.5px; line-height: 1.45; }
  .contact-list li { display: flex; align-items: center; gap: 8px; margin-bottom: 3px; }
  .icon {
    width: 18px; height: 18px;
    background: var(--ink-light);
    border-radius: 4px;
    flex: none;
  }
</style>
</head>
<body>

  <section class="card card-front" aria-label="Card front">
    <div class="wordmark">PAVREL</div>
  </section>

  <section class="card card-back" aria-label="Card back">
    <svg class="back-curve" viewBox="0 0 520 300" aria-hidden="true">
      <path d="M340 0 Q270 150 340 300" fill="none" stroke="var(--shadow)" stroke-width="6" opacity=".7"/>
      <path d="M344 0 Q276 150 344 300 L520 300 L520 0 Z" fill="var(--paper)"/>
    </svg>
    <div class="back-wordmark">PAVREL</div>
    <div class="edge-dot"></div>

    <div class="contact">
      <p class="person-name">Daniel R. Hayes</p>
      <p class="person-title">Director</p>
      <p class="address">4870 W. Canyon Rd.<br>Suite 210<br>Tucson, Arizona 85701</p>
      <ul class="contact-list">
        <li>
          <svg class="icon" viewBox="0 0 18 18" aria-hidden="true"><path d="M5.5 4 L7.5 4 L8.3 6.8 L7 7.8 Q8 10 10.2 11 L11.2 9.7 L14 10.5 L14 12.5 Q13.5 14 12 14 Q4 13 4 6 Q4 4.5 5.5 4 Z" fill="var(--forest)"/></svg>
          <span>+1 520-555-0148</span>
        </li>
        <li>
          <svg class="icon" viewBox="0 0 18 18" aria-hidden="true"><rect x="3.5" y="5" width="11" height="8" fill="none" stroke="var(--forest)" stroke-width="1.4"/><path d="M3.5 5 L9 9.5 L14.5 5" fill="none" stroke="var(--forest)" stroke-width="1.4"/></svg>
          <span>team@pavrel.com</span>
        </li>
        <li>
          <svg class="icon" viewBox="0 0 18 18" aria-hidden="true"><circle cx="9" cy="9" r="5.3" fill="none" stroke="var(--forest)" stroke-width="1.3"/><ellipse cx="9" cy="9" rx="2.3" ry="5.3" fill="none" stroke="var(--forest)" stroke-width="1.1"/><path d="M3.7 9 H14.3" stroke="var(--forest)" stroke-width="1.1"/></svg>
          <span>www.PAVREL.com</span>
        </li>
      </ul>
    </div>
  </section>

</body>
</html>
```